HearthMile business card and stationary design

We are looking for a simple yet elegant design for our mortgage company business card and stationary.

The card should include:
Name (Marcus Pell)
Title (CEO)
Phone Number (732-555-0182)
Address (48 Birchwell Court, Suite 314, Hazlet, NJ 07730)
Email (email@hearthmile.example)
"NMLS" i.e. (NMLS 61947)
"Company NMLS" (Company NMLS 274615)

Contact Information for Business Card

See above

```html
<!DOCTYPE html>
<html lang="en">
<head>
<meta charset="utf-8">
<title>HearthMile Business Card</title>
<link rel="stylesheet" href="https://fonts.googleapis.com/css2?family=Montserrat:wght@400;500;600;700&display=swap">
<style>
  :root {
    --backdrop: #8c8c8c;
    --navy: #1a2632;
    --sky: #29abe2;
    --paper: #ffffff;
    --card-w: 777px;
    --card-h: 441px;
  }
  * { margin: 0; padding: 0; box-sizing: border-box; }
  html, body {
    width: 1160px;
    height: 1200px;
    overflow: hidden;
    background: var(--backdrop);
    font-family: "Montserrat", Arial, sans-serif;
  }
  .card {
    position: absolute;
    left: 199px;
    width: var(--card-w);
    height: var(--card-h);
    border-radius: 31px;
    overflow: hidden;
  }
  .card--front { top: 105px; background: var(--paper); }
  .card--back { top: 634px; background: var(--navy); }

  .front-shapes { position: absolute; inset: 0; width: 100%; height: 100%; }

  .brand-name {
    position: absolute;
    font-weight: 600;
    white-space: nowrap;
  }
  .card--front .brand-name {
    left: 24px;
    top: 158px;
    font-size: 42px;
    color: var(--navy);
  }
  .card--back .brand-name {
    left: 0; right: 0;
    top: 196px;
    text-align: center;
    font-size: 78px;
    color: var(--paper);
  }

  .person { position: absolute; left: 387px; top: 68px; }
  .person__name {
    font-size: 28px;
    font-weight: 700;
    color: var(--sky);
    letter-spacing: -0.3px;
    line-height: 1.1;
  }
  .person__title {
    margin-top: 2px;
    font-size: 19px;
    font-weight: 700;
    color: var(--paper);
  }

  .licences {
    position: absolute;
    left: 387px;
    top: 146px;
    color: var(--paper);
    font-size: 19px;
    font-weight: 500;
    line-height: 31px;
  }

  .contacts {
    position: absolute;
    left: 387px;
    top: 223px;
    list-style: none;
    color: var(--paper);
    font-size: 19px;
    font-weight: 500;
  }
  .contacts li {
    display: flex;
    align-items: center;
    height: 30.5px;
  }
  .contacts svg { width: 19px; height: 19px; margin-right: 15px; flex: none; }

  .address {
    position: absolute;
    left: 391px;
    top: 337px;
    font-style: normal;
    color: var(--paper);
    font-size: 19px;
    font-weight: 500;
    line-height: 28px;
  }
</style>
</head>
<body>

<section class="card card--front" aria-label="Business card front">
  <svg class="front-shapes" viewBox="0 0 777 441" aria-hidden="true">
    <polygon points="387,0 777,0 777,441 257,441" fill="var(--navy)"/>
    <polygon points="376,0 382,0 252,441 246,441" fill="var(--sky)"/>
    <polygon points="338,143 777,143 777,209 318,209" fill="var(--sky)"/>
  </svg>

  <div class="brand-name">HearthMile</div>

  <div class="person">
    <div class="person__name">MARCUS PELL</div>
    <div class="person__title">CEO</div>
  </div>

  <div class="licences">
    <div>"NMLS" i.e. (NMLS 61947)</div>
    <div>Company NMLS 274615</div>
  </div>

  <ul class="contacts">
    <li>
      <svg viewBox="0 0 24 24" aria-hidden="true"><path fill="var(--sky)" d="M6.6 10.8c1.4 2.8 3.8 5.2 6.6 6.6l2.2-2.2c.3-.3.7-.4 1-.2 1.1.4 2.3.6 3.6.6.6 0 1 .4 1 1V20c0 .6-.4 1-1 1C10.6 21 3 13.4 3 4c0-.6.4-1 1-1h3.5c.6 0 1 .4 1 1 0 1.3.2 2.5.6 3.6.1.3 0 .7-.2 1z"/><path fill="none" stroke="var(--sky)" stroke-width="1.8" d="M14 3.5a7 7 0 0 1 6.5 6.5M14 7a3.5 3.5 0 0 1 3 3"/></svg>
      555-555-0182
    </li>
    <li>
      <svg viewBox="0 0 24 24" aria-hidden="true"><rect x="2" y="5" width="20" height="14" fill="var(--sky)"/><path d="M2 5l10 8 10-8" fill="none" stroke="var(--navy)" stroke-width="1.6"/></svg>
      email@hearthmile.example
    </li>
    <li>
      <svg viewBox="0 0 24 24" aria-hidden="true"><circle cx="12" cy="12" r="10" fill="var(--sky)"/><path d="M7 6c2 1 3 3 2 5s-3 2-4 1M14 14c2-1 4 0 4 2s-2 3-3 2" fill="none" stroke="var(--navy)" stroke-width="1.6"/></svg>
      www.hearthmile.example
    </li>
  </ul>

  <address class="address">
    48 Birchwell Court, Suite 314,<br>
    Alderwick, NJ 00000
  </address>
</section>

<section class="card card--back" aria-label="Business card back">
  <div class="brand-name">HearthMile</div>
</section>

</body>
</html>
```